Pilates business needs a face list flyer

We are a pilates business that has been based in England for 15 years and looking for a new flyer that is eye catch and modern but stylish
we are trying to capture the male market as well as the female market so the leaflet should draw attention to both groups.
I have attached a copy of the literature needed on the flyer also a picture of its founder

Target Market(s)

market age group 18-70+ male and female

Industry/Entity Type

Business

Font styles to use
Other font styles liked:
• calbri

Colors
33b8a4
34a7d8
3277b5
abd037

Requirements
Must have
• Literature attached
Nice to have
• To target both the male and female market. stylish but eye catching
Should not have
• pinks purples

```html
<!DOCTYPE html>
<html lang="en">
<head>
<meta charset="utf-8">
<title>Pilates Tri-fold Brochure</title>
<link href="https://fonts.googleapis.com/css2?family=Oswald:wght@300;400&family=Open+Sans:wght@400;600;700&display=swap" rel="stylesheet">
<style>
  :root{
    --teal:#1fa593;
    --teal-dark:#157d70;
    --blue:#1d4f9c;
    --sky:#2f6fb8;
    --green:#a2c93a;
    --ink:#3a3a3a;
    --grey:#5a5a5a;
    --paper:#ffffff;
    --fold:#f1f2f2;
    --bg:#e6e7e8;
  }
  *{box-sizing:border-box;margin:0;padding:0}
  html,body{width:848px;height:1200px;overflow:hidden;background:var(--bg)}
  body{position:relative;font-family:"Open Sans",Arial,sans-serif;color:var(--ink)}
  .sheet{position:absolute;left:64px;width:720px;height:560px;background:var(--paper);overflow:hidden;box-shadow:0 1px 3px rgba(0,0,0,.15)}
  .sheet--outside{top:28px}
  .sheet--inside{top:612px}
  .panel{position:absolute;top:0;width:240px;height:560px}
  .panel--left{left:0}
  .panel--middle{left:240px;background:linear-gradient(90deg,#f6f6f6,#ffffff 30%,#f3f3f3)}
  .panel--right{left:480px}
  .waves{position:absolute;left:0;top:0;width:720px;height:560px}
  .photo{position:absolute}
  .display{font-family:"Oswald",Arial,sans-serif;font-weight:300}
  p,li{font-size:7.6px;line-height:1.42;text-align:justify}

  /* schedule */
  .schedule{position:absolute;left:8px;top:12px;width:224px;text-align:center}
  .session{margin-bottom:5.4px}
  .session__time{font-size:9px;font-weight:700;color:var(--sky);line-height:1.25}
  .session__venue{font-size:8px;color:var(--ink);line-height:1.25}
  .circle{border-radius:50%;border:4px solid var(--blue)}
  .circle--cupping{left:16px;top:418px;width:112px;height:112px;background:radial-gradient(circle at 40% 60%,#d8b49a,#8a6a55 60%,#2f6e73)}
  .circle--needles{left:128px;top:400px;width:104px;height:104px;background:radial-gradient(circle at 50% 50%,#f0cdb4,#c99a7c 70%,#e8e2dc)}

  /* about */
  .about__title{position:absolute;left:18px;top:10px;font-size:12.5px;color:var(--blue)}
  .about__rule{position:absolute;left:166px;top:18px;width:62px;height:3px;background:var(--sky)}
  .about__portrait{left:18px;top:32px;width:80px;height:86px;background:linear-gradient(180deg,#cfcfcf,#8d8d8d)}
  .about__intro{position:absolute;left:104px;top:30px;width:124px}
  .about__body{position:absolute;left:18px;top:122px;width:210px}
  .about__body p{margin-bottom:4px}
  .about__backdrop{left:0;top:330px;width:240px;height:170px;background:linear-gradient(180deg,rgba(255,255,255,0),rgba(200,200,200,.45) 60%,rgba(255,255,255,0));}
  .call{position:absolute;left:0;width:240px;text-align:center;top:402px;font-size:21px;color:var(--sky);font-weight:300}
  .web{position:absolute;left:0;width:240px;text-align:center;font-size:9px;letter-spacing:2.2px;color:var(--ink)}
  .web--outside{top:438px}
  .web--inside{top:534px}

  /* cover */
  .cover__photo{left:0;top:100px;width:240px;height:410px;background:linear-gradient(160deg,#f7f3ee 10%,#e9d6c2 45%,#c79a73 70%,#f3ede6)}
  .brand{position:absolute;left:0;width:240px;text-align:center;line-height:1.08}
  .brand--cover{top:20px}
  .brand__mark{display:block;font-size:31px;color:var(--sky)}
  .brand__name{display:block;font-size:31px;color:#555}
  .brand--inside{left:240px;top:20px}
  .brand--inside .brand__mark,.brand--inside .brand__name{font-size:24px;color:#fff}

  /* inside */
  .hero{left:0;top:0;width:240px;height:150px;background:linear-gradient(180deg,#8fc6ea 0%,#bfe0f2 45%,#6b9a6a 80%,#3e7a48)}
  .col{position:absolute;top:178px;width:222px}
  .col--left{left:10px}
  .col--middle{left:249px}
  .col--right{left:489px}
  .h-section{font-size:15.5px;color:var(--sky);margin-bottom:5px}
  .h-sub{font-size:12px;font-weight:600;color:var(--teal-dark);margin:9px 0 4px}
  .col p{margin-bottom:3px}
  .benefits{list-style:none}
  .benefits li{position:relative;padding-left:9px;text-align:left;line-height:1.38}
  .benefits li::before{content:"";position:absolute;left:1px;top:4px;width:3px;height:3px;border-radius:50%;background:var(--blue)}
  .private__photo{left:480px;top:470px;width:240px;height:90px;background:linear-gradient(90deg,#6b4a3c,#c9a08a 50%,#e5d2c4)}
  .right-fade{left:480px;top:150px;width:240px;height:300px;background:radial-gradient(ellipse at 40% 30%,rgba(230,215,200,.35),rgba(255,255,255,0) 70%)}
</style>
</head>
<body>

<!-- Outside of the tri-fold -->
<section class="sheet sheet--outside">
  <div class="panel panel--left">
    <div class="schedule">
      <div class="session"><div class="session__time">Monday 10.30pm Beginner-Improver</div><div class="session__venue">The Parish Centre, Orchard Rd, Ashbridge</div></div>
      <div class="session"><div class="session__time">Monday 11.30pm Small group Class.</div><div class="session__venue">The Parish Centre, Orchard Rd, Ashbridge</div></div>
      <div class="session"><div class="session__time">Monday 6.45pm Progressive-Intermediate+</div><div class="session__venue">St Aldric Sch, The Brambles, Kelmsford</div></div>
      <div class="session"><div class="session__time">Monday 7.45pm Beginner-Improver</div><div class="session__venue">St Aldric Sch, The Brambles, Kelmsford</div></div>
      <div class="session"><div class="session__time">Tuesday 5.45pm Small group class</div><div class="session__venue">The Parish Centre, Cranford Rd, Colebrook</div></div>
      <div class="session"><div class="session__time">Tuesday 6.45pm Beginner-Improver</div><div class="session__venue">The Parish Centre, Cranford Rd, Colebrook</div></div>
      <div class="session"><div class="session__time">Wednesday 10am Progressive</div><div class="session__venue">The Parish Centre, Cranford Rd , Colebrook</div></div>
      <div class="session"><div class="session__time">Wednesday 11am&nbsp; Beginners</div><div class="session__venue">The Parish Centre, Cranford Rd, Colebrook</div></div>
      <div class="session"><div class="session__time">Wednesday 6.45pm<br>Beginner-Progressive Brindale,</div><div class="session__venue">Community Centre, Bridge St, Brindale,Nr Radley</div></div>
      <div class="session"><div class="session__time">Thursday 10am Beginner-Progressive</div><div class="session__venue">Parochial Hall, High St, Kelmsford</div></div>
      <div class="session"><div class="session__time">Thursday 6.30pm Progressive-</div><div class="session__venue">The Parish Centre, Orchard Rd, Ashbridge</div></div>
      <div class="session"><div class="session__time">Thursday 7.30pm Beginner-Progressive</div><div class="session__venue">The Parish Centre, Orchard Rd, Ashbridge</div></div>
    </div>
  </div>

  <div class="panel panel--middle">
    <div class="photo about__backdrop" role="img" aria-label="Faded photo of a woman in a pilates stretch"></div>
    <h2 class="about__title display">ABOUT MARIANNE</h2>
    <div class="about__rule"></div>
    <div class="photo about__portrait" role="img" aria-label="Portrait of the founder"></div>
    <p class="about__intro">Marianne is a one of the most experienced and a leading Pilates teacher in the Midlands. She has been studying and working within the fitness industry for 20 years. Since 1992 she has specialized in aerobics, dance and other studio-based classes.</p>
    <div class="about__body">
      <p>In 1999, Marianne received her first degree in Sport and Leisure from the University of Wessmoor. In 2000 she became the studio aerobic and fitness programme coordinator for the largest sportscentre in England</p>
      <p>2001 saw Marianne studying and complete, a Diploma in Pilates with Daniel Hart, London. In 2002, Marianne established Midshire Pilates which bases its teaching practice on a Pilates method combining up to date knowledge of exercise physiology and techniques; whilst retaining the authentic concept of the method's founder. For the past 10 years Marianne has taught Pilates locally, nationally and internationally.</p>
      <p>Since 2006 Marianne has continued with her professional development and studied Osteopathy, Traditional Acupuncture at Northgate University and Tai Chi. This wealth of knowledge and comprehensive skill-base brings a unique richness to her classes and private sessions.</p>
    </div>
    <div class="call display">CALL: 1234567890</div>
    <div class="web web--outside">www.yourwebsite.com</div>
  </div>

  <div class="panel panel--right">
    <div class="photo cover__photo" role="img" aria-label="Photo of a woman in a white dress enjoying the sun by the sea"></div>
    <div class="brand brand--cover display">
      <span class="brand__mark">LOGO</span>
      <span class="brand__name">COMPANY NAME</span>
    </div>
  </div>

  <svg class="waves" viewBox="0 0 720 560" aria-hidden="true">
    <path d="M240,505 C420,500 590,470 720,395 L720,560 L240,560Z" fill="var(--green)"/>
    <path d="M0,478 C180,472 420,520 720,440 L720,560 L0,560Z" fill="#fff"/>
    <path d="M0,484 C180,478 420,526 720,448 L720,560 L0,560Z" fill="var(--blue)"/>
    <path d="M0,500 C200,490 430,548 720,505 L720,560 L0,560Z" fill="var(--teal)"/>
  </svg>
  <div class="photo circle circle--cupping" role="img" aria-label="Photo of cupping therapy on a back"></div>
  <div class="photo circle circle--needles" role="img" aria-label="Photo of acupuncture needles"></div>
</section>

<!-- Inside of the tri-fold -->
<section class="sheet sheet--inside">
  <div class="panel panel--left">
    <div class="photo hero" role="img" aria-label="Photo of a man in a cobra stretch on grass by the sea"></div>
  </div>
  <div class="panel panel--middle"></div>
  <div class="panel panel--right">
  </div>
  <div class="photo right-fade" role="img" aria-label="Faded photo of a woman relaxing"></div>

  <svg class="waves" viewBox="0 0 720 560" aria-hidden="true">
    <path d="M240,0 H720 V78 C580,48 420,62 240,112Z" fill="var(--teal)"/>
    <path d="M0,128 C90,140 180,130 260,110 C400,72 560,52 720,80 V96 C560,70 410,92 260,126 C170,146 80,152 0,146Z" fill="var(--teal)"/>
    <path d="M260,112 C400,72 560,52 720,78 V122 C600,92 470,100 340,128 C300,136 270,132 260,112Z" fill="var(--blue)"/>
    <path d="M0,140 C100,150 200,142 300,130 L300,138 C200,152 100,160 0,152Z" fill="var(--teal)"/>
    <path d="M470,108 C580,96 660,108 720,130 V190 C650,150 570,120 470,108Z" fill="var(--green)"/>
    <path d="M480,470 C560,452 650,455 720,478 V492 C650,470 560,468 480,484Z" fill="var(--blue)"/>
  </svg>
  <div class="brand brand--inside display">
    <span class="brand__mark">LOGO</span>
    <span class="brand__name">COMPANY NAME</span>
  </div>

  <div class="col col--left">
    <h2 class="h-section display">WHAT IS PILATES?</h2>
    <p>Pilates is now the hottest and most talked about fitness trend since the aerobic explosion of the past 30 years. A perfect blend of Eastern and Western philosophy. Pilates is a holistic approach to exercise, that integrates body and mind. It concentrates on building strength stamina balance and co-ordination, improving flexibility coordination posture, breathing and well-being.</p>
    <h3 class="h-sub">Classes</h3>
    <p>All classes are based upon the original 34 movements developed by the method's founder. Classes provide low impact yet highly intense workouts, ideal for everyone, whatever age or ability or whether the individual is fit, sedentary or recuperating after illness or surgery. Furthermore, Pilates provides a safe and beneficial workout for expectant and new mothers.</p>
    <p>Each session is designed to,</p>
    <ul class="benefits">
      <li>change the way you look</li>
      <li>create lean muscles</li>
      <li>Increase strength, flexibility, coordination and proper body alignment</li>
      <li>Increase core strength</li>
      <li>Reduce fatigue, stress and risk of injury</li>
      <li>Reduce back and joint pain</li>
      <li>Rehabilitation</li>
      <li>Increase circulation</li>
      <li>Improve body mind integration</li>
    </ul>
  </div>

  <div class="col col--middle">
    <h2 class="h-section display">CLASS DESCRIPTION</h2>
    <h3 class="h-sub">Small Group Pilates (new)</h3>
    <p>This class is Structure similar to a private session. Max of 6 people allows movement plans to be more tailored to individual's needs then a larger group class. Will take from the basics and help to build on these skills to improve posture and to develop strength and flexibility. Home plan provided</p>
    <h3 class="h-sub">Beginner-Improvers</h3>
    <p>Ideal for those new to the Pilates technique. In this programme you will develop an understanding of the principals, gain strength, stamina and flexibility safely, as you are guided through a series of beginner movements, modified and tailored to your own needs and ability.</p>
    <h3 class="h-sub">Beginner-Improvers</h3>
    <p>Ideal stepping stone from beginners building on moves that you have already learnt at a more intense level, as well as learning new moves. Incorporating small equipment such as the isotoner, the stability ball, roller and Pilates balance weights to help increase the intensity of the workout without it being over challenging for those still developing their skill base.</p>
  </div>
  <div class="web web--inside" style="left:240px">www.yourwebsite.com</div>

  <div class="col col--right">
    <h3 class="h-sub" style="margin-top:0">Intermediate-Advanced</h3>
    <p>This class is designed for those already well versed in the Pilates technique. Both physically and mentally challenging, new movements are incorporated with combinations and higher intensity of known movements, alongside with the use of small equipment</p>
    <h2 class="h-section display" style="margin-top:8px">PRIVATE SESSIONS</h2>
    <p>Perfect for anyone with specific needs, restricted time frame, or limited ability. Sessions are built using the 8 Pilates principals and designed to encompass all your individual needs, with the focus upon restoring strength, flexibility, equilibrium and well being. Continued support and home movement plans are provided to help motivate and to help with achieving your goals</p>
    <p>Your private session can be arranged in the convenience of your own home or a location near to you. Please contact Marianne for further details and availability.</p>
  </div>
  <div class="photo private__photo" role="img" aria-label="Photo of an acupuncture treatment on a leg"></div>
</section>

</body>
</html>
```